New Business Card for Web Design/Internet Marketing Company

Looking for a great looking new business card. We are a 10 year old web design, internet marketing and website management company that works mostly with small businesses.

Our new card needs to better match the colors and style of our website, be bold, extremely usable and slightly edgy.

Target Market(s)

Small/Medium businesses that have websites

Industry/Entity Type

Internet

Requirements
Must have
• Front and back design, full color, rounded corners please

Must use the colors/style of our website (JPG provided)

INFO FOR CARDS (as readable as possible please)
Mark Lenner
President/CEO
mark@trelvanmedia.example
Phone: 520-381-7459
Toll Free: 866-381-7459
Address: 4315 W. Calloway Ave. Ste. 140, Tucson, AZ 85792

THINGS I WANT TO PROMOTE (if there is room):
1. Our Website - www.trelvanmedia.example

2. Social Media
Twitter: @trelvanmedia
Facebook: www.facebook.com/trelvanmedia

3. Our Services
Web Design
Internet Marketing
Website Management

```html
<!DOCTYPE html>
<html lang="en">
<head>
<meta charset="utf-8">
<title>Trelvan Media Business Card</title>
<link rel="stylesheet" href="https://fonts.googleapis.com/css2?family=Open+Sans:wght@400;600;700;800&display=swap">
<style>
  :root {
    --brand-orange: #f58634;
    --brand-blue: #0b8fc8;
    --ink-gray: #58595b;
    --card-white: #ffffff;
    --backdrop: #e9e7e4;
  }
  * { box-sizing: border-box; margin: 0; padding: 0; }
  html, body {
    width: 1200px;
    height: 421px;
    overflow: hidden;
  }
  body {
    background: var(--backdrop);
    font-family: "Open Sans", Arial, sans-serif;
    position: relative;
  }
  .card {
    position: absolute;
    top: 57px;
    width: 525px;
    height: 300px;
    overflow: hidden;
    box-shadow: 0 2px 6px rgba(0,0,0,0.18);
  }
  .card-front { left: 47px; background: var(--card-white); }
  .card-back { left: 618px; background: var(--brand-orange); color: var(--card-white); }

  .front-sweep { position: absolute; inset: 0; width: 525px; height: 300px; }

  .brand-name {
    position: absolute;
    left: 28px;
    top: 62px;
    font-size: 44px;
    font-weight: 700;
    letter-spacing: -0.5px;
    color: var(--brand-orange);
    line-height: 1;
  }
  .brand-tagline {
    position: absolute;
    right: 133px;
    top: 112px;
    font-size: 14px;
    color: var(--ink-gray);
    white-space: nowrap;
  }

  .person {
    position: absolute;
    left: 28px;
    top: 197px;
    white-space: nowrap;
  }
  .person-name {
    font-size: 19px;
    font-weight: 700;
    color: var(--brand-orange);
  }
  .person-title {
    font-size: 15px;
    color: var(--brand-blue);
  }
  .address {
    position: absolute;
    left: 28px;
    top: 246px;
    font-size: 13px;
    line-height: 17px;
    color: var(--ink-gray);
    font-style: normal;
  }

  .contact-list {
    position: absolute;
    right: 11px;
    top: 206px;
    list-style: none;
    text-align: right;
    color: var(--card-white);
    font-size: 12.5px;
    line-height: 19.5px;
  }
  .contact-list li { display: flex; justify-content: flex-end; align-items: center; gap: 5px; }
  .contact-icon { width: 10px; height: 10px; flex: none; }

  .back-brand {
    position: absolute;
    left: 0;
    right: 0;
    top: 78px;
    display: flex;
    justify-content: center;
    align-items: center;
    gap: 12px;
    font-size: 44px;
    font-weight: 700;
    letter-spacing: -0.5px;
  }
  .back-brand-dot {
    width: 22px;
    height: 22px;
    border-radius: 50%;
    background: var(--card-white);
  }
  .services {
    position: absolute;
    left: 0;
    right: 0;
    top: 193px;
    text-align: center;
    font-size: 17px;
    font-weight: 700;
    line-height: 23px;
  }
  .service::before { content: "\2022\00a0"; }
  .service + .service { margin-left: 12px; }
  .socials {
    position: absolute;
    left: 0;
    right: 0;
    top: 248px;
    text-align: center;
    font-size: 16px;
  }
  .social + .social { margin-left: 14px; }
</style>
</head>
<body>

  <section class="card card-front" aria-label="Business card front">
    <svg class="front-sweep" viewBox="0 0 525 300" aria-hidden="true">
      <path d="M458,0 C470,150 330,262 148,300 L525,300 L525,0 Z" fill="var(--brand-blue)"/>
      <path d="M525,14 C472,182 330,272 178,300 L525,300 Z" fill="var(--brand-orange)"/>
    </svg>

    <div class="brand-name">Trelvan Media</div>
    <div class="brand-tagline">Build your Presence</div>

    <p class="person">
      <span class="person-name">Mark Lenner ,</span>
      <span class="person-title">President/CEO</span>
    </p>
    <address class="address">
      4315 W. Calloway Ave. Ste. 140<br>
      Tucson, AZ 85792
    </address>

    <ul class="contact-list">
      <li>866-381-7459
        <svg class="contact-icon" viewBox="0 0 10 10" aria-hidden="true"><circle cx="5" cy="5" r="4.3" fill="none" stroke="#fff" stroke-width="1"/><path d="M3.4,2.6 L4.4,2.6 L4.6,3.9 L4,4.4 C4.3,5.1 4.9,5.7 5.6,6 L6.1,5.4 L7.4,5.6 L7.4,6.6 C5.2,7 3,4.8 3.4,2.6 Z" fill="#fff"/></svg>
      </li>
      <li>520-381-7459
        <svg class="contact-icon" viewBox="0 0 10 10" aria-hidden="true"><circle cx="5" cy="5" r="4.3" fill="none" stroke="#fff" stroke-width="1"/><path d="M3.4,2.6 L4.4,2.6 L4.6,3.9 L4,4.4 C4.3,5.1 4.9,5.7 5.6,6 L6.1,5.4 L7.4,5.6 L7.4,6.6 C5.2,7 3,4.8 3.4,2.6 Z" fill="#fff"/></svg>
      </li>
      <li>mark@trelvanmedia.example
        <svg class="contact-icon" viewBox="0 0 10 10" aria-hidden="true"><circle cx="5" cy="5" r="5" fill="#fff"/><rect x="2.4" y="3.3" width="5.2" height="3.6" fill="var(--brand-orange)"/><path d="M2.4,3.3 L5,5.3 L7.6,3.3" fill="none" stroke="#fff" stroke-width="0.7"/></svg>
      </li>
      <li>www.trelvanmedia.example
        <svg class="contact-icon" viewBox="0 0 10 10" aria-hidden="true"><circle cx="5" cy="5" r="5" fill="#fff"/><path d="M1,5 H9 M5,1 V9 M1.8,3 H8.2 M1.8,7 H8.2" stroke="var(--brand-orange)" stroke-width="0.6" fill="none"/></svg>
      </li>
    </ul>
  </section>

  <section class="card card-back" aria-label="Business card back">
    <div class="back-brand"><span class="back-brand-dot"></span>Trelvan Media</div>
    <div class="services">
      <span class="service">Web Design</span><span class="service">Internet Marketing</span><br>
      <span class="service">Website Management</span>
    </div>
    <div class="socials">
      <span class="social">@trelvanmedia</span><span class="social">trelvanmedia</span>
    </div>
  </section>

</body>
</html>
```